dsadasdasdasdsa

Industry/Entity Type

Mortgage Broking

Requirements
Must have
• Call-to-action button somewhere on the graphic
Nice to have
• The font of our logo is Montserrat

```html
<!DOCTYPE html>
<html lang="en">
<head>
<meta charset="utf-8">
<title>Mortgage Broker Directory Banner</title>
<link rel="stylesheet" href="https://fonts.googleapis.com/css2?family=Montserrat:wght@600;700;800;900&display=swap">
<style>
  :root {
    --mint-light: #e6fbf3;
    --mint: #8ff0c6;
    --green-start: #1f8f4f;
    --green-end: #157a42;
    --red: #bf3a26;
    --yellow: #f4f21c;
    --white: #ffffff;
    --mascot-shell: #7a4a22;
    --mascot-skin: #4fae45;
  }
  * { margin: 0; padding: 0; box-sizing: border-box; }
  html, body {
    width: 1200px;
    height: 180px;
    overflow: hidden;
  }
  body {
    font-family: "Montserrat", sans-serif;
  }
  .banner {
    position: relative;
    width: 1200px;
    height: 180px;
    background: linear-gradient(180deg, var(--mint-light) 0%, var(--mint) 100%);
    overflow: hidden;
  }
  .banner__band {
    position: absolute;
    left: 36px;
    top: 22px;
    width: 1160px;
    height: 138px;
    border-radius: 22px;
    overflow: hidden;
    background: var(--red);
  }
  .banner__band-green {
    position: absolute;
    left: 0;
    top: 0;
    width: 726px;
    height: 100%;
    background: linear-gradient(90deg, var(--green-start) 0%, var(--green-end) 100%);
  }
  .banner__copy {
    position: absolute;
    left: 74px;
    top: 40px;
  }
  .banner__eyebrow {
    color: var(--yellow);
    font-weight: 600;
    font-size: 26px;
    line-height: 30px;
    letter-spacing: 0.2px;
  }
  .banner__headline {
    margin-top: 6px;
    color: var(--white);
    font-weight: 800;
    font-size: 31px;
    line-height: 33px;
    text-transform: uppercase;
    letter-spacing: 0.3px;
  }
  .banner__mascot {
    position: absolute;
    left: 730px;
    top: 8px;
    width: 150px;
    height: 170px;
    border-radius: 48% 48% 40% 40%;
    background: radial-gradient(ellipse at 40% 35%, var(--mascot-skin) 0%, #3d8f3a 55%, var(--mascot-shell) 100%);
  }
  .banner__cta {
    position: absolute;
    left: 988px;
    top: 73px;
    width: 178px;
    height: 42px;
    border: 2px solid var(--white);
    border-radius: 21px;
    display: flex;
    align-items: center;
    justify-content: center;
    color: var(--yellow);
    font-weight: 800;
    font-size: 17px;
    letter-spacing: 0.3px;
    text-decoration: none;
    text-transform: uppercase;
  }
</style>
</head>
<body>
  <div class="banner">
    <div class="banner__band">
      <div class="banner__band-green"></div>
    </div>
    <div class="banner__copy">
      <p class="banner__eyebrow">Need a Mortgage Broker?</p>
      <h1 class="banner__headline">Search now on Australia’s<br>largest directory</h1>
    </div>
    <div class="banner__mascot" role="img" aria-label="Cartoon turtle mascot holding a small house with a red roof"></div>
    <a class="banner__cta" href="#">Click here</a>
  </div>
</body>
</html>
```